Brovick Engineering Core Values Branding Package

Brovick Engineering has recently refined its company Core Values and is seeking a strong, cohesive branding package to visually bring these values to life. The new graphic assets will communicate our commitment to excellence in a way that resonates with our team, clients, and partners in a blue-collar, industrial environment.

We are looking for multiple visual assets with consistent design elements that can be applied across platforms. The tone should reflect strength, reliability, and professionalism while remaining approachable and aligned with our industry.

Core Values & Descriptions
Accountability
“We take ownership of our work and actions, ensuring reliability and trust in every solution we deliver.”

Teamwork
“We collaborate across departments and disciplines to provide the highest level of service and innovation for our clients.”

Integrity
“We operate with honesty, transparency, and ethical standards in all aspects of our business.”

Growth
“We are committed to continuous improvement—of our people, our processes, and our impact in the industry.”

Deliverables

1. Primary Core Values Graphic
A master visual representing all four values together.
Designed for use on posters, office signage, internal presentations.

2. Individual Value Graphics (x4)
One graphic per core value: Accountability, Teamwork, Integrity, Growth.
Cohesive style with slight visual variation to reflect each value’s unique meaning.

Target Market(s)

Employees of Brovick Engineering

Industry/Entity Type

Blue Collar

Font styles to use
Sans Serif

Colors
0054AA
0677BA
7BADD7
CADEEF
E8F1F8
00AB8E
00BBA5
67D7C9
C6EFE9
E9F9F6
EB3D1F
EC4F4E
F09395
F8D3D4
FCEDEE

Requirements
Must have
• Accountability, Teamwork, Integrity, Growth

```html
<!DOCTYPE html>
<html lang="en">
<head>
<meta charset="utf-8">
<title>Brovick Engineering — Core Values</title>
<link rel="stylesheet" href="https://fonts.googleapis.com/css2?family=Roboto+Condensed:wght@300;400;700;800&display=swap">
<style>
  :root {
    --navy: #1b3b6f;
    --green: #3aa845;
    --gold: #e4a63a;
    --red: #c51c2e;
    --ink: #2b2b2b;
    --paper: #ffffff;
    --backdrop: #e6e6e6;
    --dots: #a9a9a9;
  }
  * { box-sizing: border-box; margin: 0; padding: 0; }
  html, body { width: 1200px; height: 1200px; overflow: hidden; }
  body {
    background: var(--backdrop);
    font-family: "Roboto Condensed", "Arial Narrow", sans-serif;
    position: relative;
  }
  .poster {
    position: absolute;
    left: 165px; top: 29px;
    width: 870px; height: 1142px;
    background: var(--paper);
    overflow: hidden;
  }
  .brand {
    position: absolute; left: 0; right: 0; top: 92px;
    text-align: center;
    font-weight: 800; font-size: 76px; letter-spacing: 2px;
    color: var(--navy); line-height: 1;
  }
  .title {
    position: absolute; left: 0; right: 0; top: 255px;
    text-align: center;
    font-weight: 800; font-size: 92px; line-height: 1;
    color: var(--navy); letter-spacing: 1px;
  }
  .tag {
    position: absolute; height: 53px;
    color: #fff; font-weight: 700; font-size: 40px; line-height: 53px;
    text-align: center; letter-spacing: -0.5px;
    border-radius: 14px 0 14px 0;
  }
  .tag--people { left: 76px; top: 354px; width: 351px; background: var(--navy); }
  .tag--solutions { left: 441px; top: 354px; width: 352px; background: var(--green); }
  .tag--now { left: 295px; top: 420px; width: 280px; background: var(--red); }

  .value { position: absolute; width: 210px; }
  .value h2 { font-weight: 700; font-size: 40px; line-height: 1; letter-spacing: -0.5px; white-space: nowrap; }
  .value p {
    margin-top: 22px; font-size: 17px; line-height: 23px;
    color: var(--ink); font-weight: 400; letter-spacing: -0.3px;
    white-space: nowrap;
  }
  .value--left { left: 76px; text-align: left; }
  .value--right { right: 77px; text-align: right; }
  .value--right h2 { margin-left: -60px; }
  .value--accountability { top: 530px; } .value--accountability h2 { color: var(--navy); }
  .value--teamwork { top: 530px; } .value--teamwork h2 { color: var(--gold); }
  .value--growth { top: 744px; } .value--growth h2 { color: var(--green); }
  .value--integrity { top: 744px; } .value--integrity h2 { color: var(--red); }

  .leaders { position: absolute; left: 0; top: 0; }
  .values-wheel { position: absolute; left: 262px; top: 565px; }
  .invite {
    position: absolute; left: 76px; top: 1000px;
    font-size: 24px; line-height: 31px; font-weight: 400;
    color: var(--green);
  }
</style>
</head>
<body>
  <main class="poster">
    <div class="brand">BROVICK</div>
    <h1 class="title">CORE VALUES</h1>

    <div class="tag tag--people">The Right People</div>
    <div class="tag tag--solutions">The Right Solutions</div>
    <div class="tag tag--now">Right Now!</div>

    <svg class="leaders" width="870" height="1142" aria-hidden="true">
      <g fill="none" stroke="var(--dots)" stroke-width="3" stroke-linecap="round" stroke-dasharray="0 7">
        <path d="M76 577 H309 V609"/>
        <path d="M793 577 H562 V609"/>
        <path d="M76 793 H263"/>
        <path d="M793 793 H605"/>
      </g>
    </svg>

    <section class="value value--left value--accountability">
      <h2>Accountability</h2>
      <p>We take ownership of our<br>work and actions, ensuring<br>reliability and trust in every<br>solution we deliver.</p>
    </section>
    <section class="value value--right value--teamwork">
      <h2>Teamwork</h2>
      <p>We collaborate across<br>departments and disciplines<br>to provide the highest level<br>of service and innovation for<br>our clients.</p>
    </section>
    <section class="value value--left value--growth">
      <h2>Growth</h2>
      <p>We are committed to<br>continuous improvement—of<br>our people, our processes, and<br>our impact in the industry.”</p>
    </section>
    <section class="value value--right value--integrity">
      <h2>Integrity</h2>
      <p>We operate with honesty,<br>transparency, and ethical<br>standards in all aspects of<br>our business.</p>
    </section>

    <svg class="values-wheel" width="346" height="346" viewBox="0 0 346 346">
      <path role="img" aria-label="Accountability quadrant with icon of a hand holding a report" d="M163 163 H13 A150 150 0 0 1 163 13 Z" fill="var(--navy)"/>
      <path role="img" aria-label="Teamwork quadrant with icon of people climbing bars to a flag" d="M183 163 V13 A150 150 0 0 1 333 163 Z" fill="var(--gold)"/>
      <path role="img" aria-label="Growth quadrant with icon of a rising bar chart" d="M163 183 V333 A150 150 0 0 1 13 183 Z" fill="var(--green)"/>
      <path role="img" aria-label="Integrity quadrant with icon of hands holding a shield" d="M183 183 H333 A150 150 0 0 1 183 333 Z" fill="var(--red)"/>
    </svg>

    <p class="invite">Be a bright part of our organization.<br>Become involved and demonstrate<br>you have the right stuff.</p>
  </main>
</body>
</html>
```